Veluxa Bone & Motion Business Card

Need a business card using the logo provided. I want brand side of the card to be grey with the logo in the center of the card in white.

On the other side I leave to the designers

Target Market(s)

Personal Injury Attorneys

Industry/Entity Type

Medical

Contact Information for Business Card

Name, CEO. Cell Phone, (Hialeah, Address, Phone) (Homestead, Address, Phone) (Tallahassee, Address, Phone)

Colors

Designer to choose only greyscale colors for use in the design.

Requirements
Must have
• Logo by itself on one side

```html
<!DOCTYPE html>
<html lang="en">
<head>
<meta charset="utf-8">
<title>Veluxa Bone &amp; Motion Business Card</title>
<link rel="stylesheet" href="https://fonts.googleapis.com/css2?family=Montserrat:wght@400;500;700&display=swap">
<style>
  :root {
    --backdrop: #3a3b3e;
    --card-grey: #a4a8ab;
    --card-white: #ffffff;
    --accent: #4b5055;
    --ink: #1f2326;
    --light: #ffffff;
  }
  * { box-sizing: border-box; margin: 0; padding: 0; }
  html, body {
    width: 1200px; height: 801px; overflow: hidden;
    background: var(--backdrop);
    font-family: "Montserrat", sans-serif;
  }
  .stage {
    position: relative; width: 1200px; height: 801px;
    display: flex; align-items: center; justify-content: center; gap: 50px;
  }
  .card {
    position: relative; width: 540px; height: 309px;
    border-radius: 14px; overflow: hidden;
    box-shadow: 0 10px 26px rgba(0,0,0,.35);
  }
  /* Brand side */
  .card--brand {
    background: var(--card-grey);
    display: flex; align-items: center; justify-content: center;
  }
  .brand-name {
    display: flex; align-items: center; gap: 16px;
    color: var(--light);
    font-weight: 500; text-transform: uppercase;
  }
  .brand-name__words { display: flex; flex-direction: column; line-height: 1.15; }
  .brand-name__main { font-size: 44px; letter-spacing: .14em; }
  .brand-name__sub { font-size: 20px; letter-spacing: .2em; padding-left: 4px; }
  .brand-dot {
    width: 14px; height: 14px; border-radius: 50%;
    background: var(--light);
  }
  /* Contact side */
  .card--contact { background: var(--card-white); }
  .contact-bg { position: absolute; inset: 0; }
  .identity {
    position: absolute; left: 36px; top: 56px; color: var(--light);
  }
  .identity__brand { font-weight: 500; text-transform: uppercase; line-height: 1.15; }
  .identity__main { font-size: 26px; letter-spacing: .14em; }
  .identity__sub { font-size: 13px; letter-spacing: .2em; }
  .person { margin-top: 46px; }
  .person__name { font-weight: 700; font-size: 24px; }
  .person__role { font-weight: 500; font-size: 15px; margin: 4px 0 6px 60px; }
  .person__phone {
    display: flex; align-items: center; gap: 6px;
    font-weight: 500; font-size: 16px; letter-spacing: .05em; margin-left: 40px;
  }
  .locations {
    position: absolute; right: 24px; top: 22px;
    text-align: right; display: flex; flex-direction: column; gap: 16px;
  }
  .location__city {
    color: var(--accent); font-weight: 700; font-size: 13px; letter-spacing: .03em;
  }
  .location__address { color: var(--ink); font-size: 11px; line-height: 1.35; }
  .location__phone {
    color: var(--accent); font-weight: 700; font-size: 14px; letter-spacing: .04em;
  }
</style>
</head>
<body>
<main class="stage">
  <section class="card card--brand" aria-label="Brand side">
    <div class="brand-name">
      <span class="brand-dot"></span>
      <span class="brand-name__words">
        <span class="brand-name__main">Veluxa</span>
        <span class="brand-name__sub">Bone &amp; Motion</span>
      </span>
    </div>
  </section>

  <section class="card card--contact" aria-label="Contact side">
    <svg class="contact-bg" width="540" height="309" viewBox="0 0 540 309">
      <path d="M0,0 H300 Q320,230 470,309 H0 Z" fill="var(--card-grey)"/>
      <path d="M292,0 Q312,236 462,309 L430,309 Q285,236 268,0 Z"
            fill="var(--accent)" role="img" aria-label="Spine vertebrae illustration along the curve"/>
    </svg>

    <div class="identity">
      <div class="identity__brand">
        <div class="identity__main">Veluxa</div>
        <div class="identity__sub">Bone &amp; Motion</div>
      </div>
      <div class="person">
        <div class="person__name">Dr.Name</div>
        <div class="person__role">CEO</div>
        <div class="person__phone">
          <svg width="14" height="14" viewBox="0 0 24 24" aria-hidden="true"><path fill="currentColor" d="M6.6 10.8a15.1 15.1 0 0 0 6.6 6.6l2.2-2.2a1 1 0 0 1 1-.25 11.4 11.4 0 0 0 3.6.57 1 1 0 0 1 1 1V20a1 1 0 0 1-1 1A17 17 0 0 1 3 4a1 1 0 0 1 1-1h3.5a1 1 0 0 1 1 1c0 1.25.2 2.45.57 3.57a1 1 0 0 1-.25 1z"/></svg>
          0123 456 789
        </div>
      </div>
    </div>

    <div class="locations">
      <div class="location">
        <div class="location__city">HIALEAH</div>
        <div class="location__address">1450 Palm Crest Ave #310<br>Hialeah, FL 33012</div>
        <div class="location__phone">954-555-0142</div>
      </div>
      <div class="location">
        <div class="location__city">HOMESTEAD</div>
        <div class="location__address">1450 Palm Crest Ave #310<br>Homestead, FL 33030</div>
        <div class="location__phone">954-555-0142</div>
      </div>
      <div class="location">
        <div class="location__city">TALLAHASSEE</div>
        <div class="location__address">1450 Palm Crest Ave #310<br>Tallahassee, FL 32301</div>
        <div class="location__phone">954-555-0142</div>
      </div>
    </div>
  </section>
</main>
</body>
</html>
```